Business Card for Field Lotus-Eco Friendly Organic Clothing Brand

We are looking for an amazing business card for our eco friendly, organic clothing brand. We are thinking maybe a business card with a peel off sticker on the back, since our hanging clothing tag is a peel off sticker on the back. I will attach our hang tag so we can make sure we stay in line with our design. I've also attached a bag we are doing because I do like the scattered emblem look as well.

```html
<!DOCTYPE html>
<html lang="en">
<head>
<meta charset="utf-8">
<title>Field Lotus – Business Card</title>
<link rel="stylesheet" href="https://fonts.googleapis.com/css2?family=Open+Sans:wght@400;600&display=swap">
<style>
  :root {
    --page-bg: #e8e5e1;
    --card-white: #ffffff;
    --ink-dark: #1f2118;
    --gold-deep: #c79a34;
    --gold-mid: #dcbc63;
    --gold-light: #efdb9a;
    --text-white: #ffffff;
  }
  * { margin: 0; padding: 0; box-sizing: border-box; }
  html, body {
    width: 1200px;
    height: 900px;
    overflow: hidden;
    background: var(--page-bg);
    font-family: "Open Sans", sans-serif;
  }
  .business-card {
    position: absolute;
    left: 145px;
    top: 170px;
    width: 910px;
    height: 561px;
    background: var(--card-white);
    overflow: hidden;
    box-shadow: 0 6px 24px rgba(0, 0, 0, 0.18);
  }
  .card-wave {
    position: absolute;
    inset: 0;
    width: 100%;
    height: 100%;
  }
  .holder {
    position: absolute;
    right: 60px;
    top: 52px;
    text-align: right;
  }
  .holder-name {
    font-size: 36px;
    font-weight: 600;
    color: var(--gold-deep);
    line-height: 1.1;
    letter-spacing: 0.3px;
  }
  .holder-title {
    font-size: 22px;
    font-weight: 400;
    color: var(--ink-dark);
    line-height: 1.3;
  }
  .brand {
    position: absolute;
    left: 62px;
    top: 178px;
    display: flex;
    align-items: center;
    gap: 18px;
  }
  .brand-mark {
    width: 54px;
    height: 54px;
    background: var(--ink-dark);
  }
  .brand-name {
    font-size: 44px;
    font-weight: 600;
    color: var(--ink-dark);
    line-height: 1;
  }
  .brand-url {
    position: absolute;
    left: 134px;
    top: 246px;
    font-size: 14px;
    color: var(--ink-dark);
  }
  .contact-list {
    position: absolute;
    right: 58px;
    top: 352px;
    list-style: none;
  }
  .contact-item {
    display: flex;
    justify-content: flex-end;
    align-items: center;
    gap: 12px;
    height: 37.5px;
    font-size: 23px;
    color: var(--text-white);
  }
  .contact-icon {
    width: 28px;
    height: 28px;
    flex: none;
  }
</style>
</head>
<body>
  <section class="business-card">
    <svg class="card-wave" viewBox="0 0 652 402" preserveAspectRatio="none" aria-hidden="true">
      <defs>
        <linearGradient id="goldFill" x1="0" y1="0" x2="0" y2="1">
          <stop offset="0" stop-color="#c99d3a"/>
          <stop offset="0.55" stop-color="#efdb9a"/>
          <stop offset="1" stop-color="#c79a34"/>
        </linearGradient>
      </defs>
      <path fill="var(--ink-dark)" d="M0,210 C70,268 120,318 190,312 C320,300 430,108 540,108 C600,108 640,140 652,160 L652,402 L0,402 Z"/>
      <path fill="var(--card-white)" d="M0,224 C70,288 120,330 190,325 C320,314 430,124 540,124 C600,124 640,156 652,174 L652,402 L0,402 Z"/>
      <path fill="url(#goldFill)" d="M0,232 C70,298 120,338 190,333 C320,322 430,134 540,134 C600,134 640,164 652,180 L652,402 L0,402 Z"/>
    </svg>

    <header class="holder">
      <h1 class="holder-name">Jonathan Smith</h1>
      <p class="holder-title">Managing Director</p>
    </header>

    <div class="brand">
      <span class="brand-mark"></span>
      <span class="brand-name">Field Lotus</span>
    </div>
    <p class="brand-url">www.fieldlotus.com</p>

    <ul class="contact-list">
      <li class="contact-item">044-456-7890
        <svg class="contact-icon" viewBox="0 0 28 28" aria-hidden="true"><rect x="2" y="2" width="24" height="24" rx="3" fill="#fff"/><path d="M7 12 Q14 6 21 12 L19 14 L17 12 L11 12 L9 14 Z M9 15 H19 V21 H9 Z" fill="#c79a34"/></svg>
      </li>
      <li class="contact-item">123-456-7890
        <svg class="contact-icon" viewBox="0 0 28 28" aria-hidden="true"><rect x="2" y="2" width="24" height="24" rx="3" fill="#fff"/><rect x="8" y="6" width="12" height="16" rx="1" fill="#c79a34"/><rect x="10" y="8" width="8" height="5" fill="#fff"/><rect x="10" y="15" width="8" height="1.6" fill="#fff"/><rect x="10" y="18" width="8" height="1.6" fill="#fff"/></svg>
      </li>
      <li class="contact-item">123-456-7890
        <svg class="contact-icon" viewBox="0 0 28 28" aria-hidden="true"><rect x="2" y="2" width="24" height="24" rx="3" fill="#fff"/><rect x="9" y="5" width="10" height="18" rx="2" fill="#c79a34"/><rect x="11" y="8" width="6" height="10" fill="#fff"/><circle cx="14" cy="20.5" r="1" fill="#fff"/></svg>
      </li>
      <li class="contact-item">info@youremail.com
        <svg class="contact-icon" viewBox="0 0 28 28" aria-hidden="true"><rect x="2" y="2" width="24" height="24" rx="3" fill="#fff"/><rect x="6" y="8" width="16" height="12" fill="#c79a34"/><path d="M6 8 L14 15 L22 8" fill="none" stroke="#fff" stroke-width="1.6"/></svg>
      </li>
      <li class="contact-item">www.website.com
        <svg class="contact-icon" viewBox="0 0 28 28" aria-hidden="true"><rect x="2" y="2" width="24" height="24" rx="3" fill="#fff"/><path d="M12 16 L16 12 M11 13 L8.5 15.5 A2.5 2.5 0 0 0 12.5 19.5 L15 17 M13 11 L15.5 8.5 A2.5 2.5 0 0 1 19.5 12.5 L17 15" fill="none" stroke="#c79a34" stroke-width="2" stroke-linecap="round"/></svg>
      </li>
    </ul>
  </section>
</body>
</html>
```